Taro Reserve website (www.taroreserve.com)

My company develops booking software, Taro Reserve, for the hourly booking of resources such as classes in a school or customer booking involving rooms in a spa. These bookings also involve the customers, staff, rooms and a lesson or treatment.

The main difference between this software and general calendar software such as Plonkit calendar is that this Taro Reserve allows resources such as people and rooms to be associated with the bookings. This is important for example in the case of a Spa to make sure the rooms are booked appropriately and to see the free times for the rooms. For a golf practice range the players much be booked to the tee spots where they practice golf.

I have tried to design the website myself, as a computer programmer- I am a bit "square" and not a designer, my first attempt is http://www.taroreserve.com/, my second attempt is at http://www.lumex-works.com/taroreservewebsite/
I am not happy with my designs as compared to the professional designs I see people can come up with here. The software must have the image of a professional software product in order to inspire the confidence of customers.

Am looking for a design which will be the most likely to give the customer the following feeling:
* Confident the product can do the job.
* Feel easy to want to try it, at least for the free trial.
* Its a professional software product and also a web based product, the user can login from the web.

Look at other booking software websites for ideas, here is a list of links to similar booking products. These products all have different features but are mostly for resource booking.
http://lumex-works.com/taroreservewebsite/?page=compare
Updates

Hello all,

Thankyou for the designs so far, to save peoples time, I will try to eliminate the bottom 50% of designs now.

To be honest, most of the designs are of a good or high quality, I think its very tough on you as graphic and web designers. Only a minor few are of low quality.

If your design is discarded - I would say its unlikely that you are going to be able to produce a design that will beat the competition. 
You probably already know, you could try to re-sell your design later for other projects or as a template on one of those template websites. Some of these discarded designs are quite worthwhile designs.

Best regards, Gordon

Target Market(s)

Spa, Gym, School, Golf, any organization who manages bookings of their customers

Industry/Entity Type

Software

Requirements
Must have
• Home page and inner page, any other pages up to you.

Make a logo or use the image of the girl that I already have on the second design.

Menu(s) for navigation.

A language switcher for 3 languages, English, Chinese Traditional and Chinese Simplified. (Western, Hong Kong and Chinese mainland market are important).

Space for a video introduction, it could be small and when the user clicks on it then it gets bigger then it won't take up too much space. Up to you.

A space for the user to login and register a new account.

Screenshots.

I don't have any strong preferences, use your own ideas, if you look at all the other products you can get the basic idea from them.

The total goal is to make a website which is going to lead to sales of the software product.

```html
<!DOCTYPE html>
<html lang="en">
<head>
<meta charset="utf-8">
<title>Taro Reserve — Bookings Schedule</title>
<link rel="stylesheet" href="https://fonts.googleapis.com/css2?family=Nunito:wght@400;600;700;800&display=swap">
<style>
  :root {
    --page-light: #f4fbfd;
    --page-mid: #cfe9f1;
    --page-edge: #9fd1e0;
    --band: #5fa9bd;
    --band-text: #ffffff;
    --copyright: #2f6f82;
    --tab-top: #6fb4c8;
    --tab-bottom: #4c97ad;
    --tab-active: #f4f4f4;
    --binder: #2f3133;
    --paper: #ffffff;
    --paper-edge: #dcdcdc;
    --step-bg: #f2f2f2;
    --step-line: #d5d5d5;
    --step-text: #9a9a9a;
    --step-active: #3d3d3d;
    --cal-head-top: #6fb7cb;
    --cal-head-bottom: #3f8ea6;
    --col-head: #e6e6e6;
    --grid-line: #dedede;
    --text: #6b6b6b;
    --text-dark: #555555;
    --booking-blue: #a7e0ea;
    --booking-mint: #a9eadf;
    --mascot-warm: #c98a63;
    --mascot-soft: #efd2bc;
    --sign: #ffffff;
  }
  * { box-sizing: border-box; margin: 0; padding: 0; }
  html, body { width: 1200px; height: 900px; overflow: hidden; }
  body {
    position: relative;
    font-family: "Nunito", "Helvetica Neue", Arial, sans-serif;
    color: var(--text);
    background: radial-gradient(ellipse 70% 60% at 50% 55%, var(--page-light) 0%, var(--page-mid) 70%, var(--page-edge) 100%);
  }

  /* language switcher */
  .language {
    position: absolute; top: 10px; left: 918px;
    display: flex; align-items: center; gap: 8px;
    font-size: 13px; color: #4a6a74;
  }
  .language .option { display: flex; align-items: center; gap: 4px; }
  .radio {
    width: 12px; height: 12px; border-radius: 50%;
    background: #fff; border: 1px solid #9ab; display: inline-block; position: relative;
  }
  .radio.checked::after {
    content: ""; position: absolute; inset: 2px; border-radius: 50%; background: #555;
  }

  /* binder frame */
  .binder {
    position: absolute; left: 87px; top: 96px; width: 1017px; height: 130px;
    background: var(--binder); border-radius: 14px 14px 0 0;
  }
  .page-left {
    position: absolute; left: 105px; top: 123px; width: 288px; height: 100px;
    background: var(--paper); border-radius: 4px 0 0 0;
  }
  .page-right {
    position: absolute; left: 404px; top: 123px; width: 662px; height: 100px;
    background: var(--paper); border-radius: 0 4px 0 0;
    box-shadow: 3px 0 0 #e9e9e9, 6px 0 0 #d8d8d8;
  }
  .rings { position: absolute; left: 380px; top: 172px; }

  /* mascot area and sign */
  .mascot {
    position: absolute; left: 186px; top: 33px; width: 106px; height: 118px;
    border-radius: 8px;
    background: linear-gradient(180deg, var(--mascot-warm) 0%, var(--mascot-soft) 100%);
  }
  .sign {
    position: absolute; left: 129px; top: 146px; width: 222px; height: 64px;
    background: var(--sign); border: 1px solid var(--paper-edge);
    display: flex; align-items: center; justify-content: center;
    box-shadow: 0 1px 3px rgba(0,0,0,.2);
  }
  .brand-name { font-size: 27px; font-weight: 400; color: #4a4a4a; letter-spacing: .5px; }

  /* main navigation tabs */
  .main-nav { position: absolute; top: 86px; left: 408px; display: flex; gap: 5px; }
  .main-nav a {
    height: 37px; display: flex; align-items: center; justify-content: center;
    color: #fff; font-weight: 800; font-size: 15px; text-decoration: none;
    background: linear-gradient(180deg, var(--tab-top), var(--tab-bottom));
    border-radius: 3px 3px 0 0; text-shadow: 0 1px 0 rgba(0,0,0,.2);
  }
  .main-nav a.active { background: var(--tab-active); color: #333; text-shadow: none; }

  /* booking steps */
  .steps {
    position: absolute; left: 447px; top: 146px; width: 580px; height: 47px;
    display: flex; background: var(--step-bg);
    border: 1px solid #dedede; border-radius: 3px;
  }
  .step {
    flex: 1; position: relative; display: flex; align-items: center; justify-content: center;
    font-size: 14px; color: var(--step-text); padding-right: 18px;
  }
  .step .label { position: relative; z-index: 2; white-space: nowrap; }
  .step.current { color: var(--step-active); font-weight: 600; }
  .step:not(:last-child) .chevron {
    position: absolute; right: -8px; top: 0; width: 22px; height: 45px; z-index: 1;
  }

  /* calendar */
  .calendar {
    position: absolute; left: 41px; top: 211px; width: 1113px; height: 621px;
    background: #f1f1f1; border: 1px solid #bdbdbd;
    box-shadow: 0 2px 8px rgba(0,0,0,.25); padding: 3px;
  }
  .cal-title {
    height: 27px; display: flex; align-items: center; justify-content: center; gap: 22px;
    color: #fff; font-weight: 700; font-size: 15px;
    background: linear-gradient(180deg, var(--cal-head-top), var(--cal-head-bottom));
    border-radius: 2px 2px 0 0;
  }
  .cal-title .arrow { font-size: 10px; }
  .cal-columns, .cal-body {
    display: grid;
    grid-template-columns: 144px 182px 192px 189px 194px 203px;
  }
  .cal-columns {
    height: 31px; background: linear-gradient(180deg, #f2f2f2, var(--col-head));
    border-bottom: 1px solid #cfcfcf;
  }
  .cal-columns span {
    display: flex; align-items: center; justify-content: center;
    font-size: 14px; color: var(--text);
  }
  .cal-body {
    grid-template-rows: repeat(17, 31px);
    background-color: var(--paper);
    background-image: repeating-linear-gradient(180deg, transparent 0 30px, var(--grid-line) 30px 31px);
  }
  .col-line { grid-row: 1 / 18; border-left: 1px solid var(--grid-line); }
  .time {
    grid-column: 1; display: flex; align-items: center; justify-content: center;
    font-size: 14px; color: var(--text); padding-right: 14px;
  }
  .booking {
    position: relative; z-index: 1; margin: 0 0 1px 1px;
    padding: 10px 16px; font-size: 13px; line-height: 20px; color: var(--text);
  }
  .booking.single { background: var(--booking-blue); }
  .booking.group { background: var(--booking-mint); }
  .booking h3 { font-size: 14px; font-weight: 700; color: var(--text-dark); margin-bottom: 1px; }
  .booking ul { list-style: none; }
  .booking li::before { content: "- "; }
  .cal-foot {
    height: 30px; background: linear-gradient(180deg, #ececec, #dcdcdc);
    border-top: 1px solid #cfcfcf;
  }

  /* footer */
  .site-footer {
    position: absolute; left: 0; bottom: 0; width: 1200px; height: 39px;
    background: var(--band); display: flex; align-items: center;
  }
  .footer-nav { display: flex; gap: 27px; margin-left: 104px; }
  .footer-nav a { color: var(--band-text); font-weight: 600; font-size: 14px; text-decoration: none; }
  .copyright { position: absolute; left: 975px; font-size: 13px; font-weight: 700; color: var(--copyright); }
</style>
</head>
<body>

  <div class="language">
    <span>Language:</span>
    <span class="option"><i class="radio checked"></i>English</span>
    <span class="option"><i class="radio"></i>体 体</span>
    <span class="option"><i class="radio"></i>繁體</span>
  </div>

  <div class="binder"></div>
  <div class="page-left"></div>
  <div class="page-right"></div>

  <div class="mascot" role="img" aria-label="Brand mascot illustration holding the name sign"></div>
  <div class="sign"><span class="brand-name">Taro Reserve</span></div>

  <svg class="rings" width="36" height="40" viewBox="0 0 36 40" aria-hidden="true">
    <rect x="2" y="3" width="32" height="10" rx="5" fill="none" stroke="#222" stroke-width="3"/>
    <rect x="2" y="19" width="32" height="10" rx="5" fill="none" stroke="#222" stroke-width="3"/>
  </svg>

  <nav class="main-nav">
    <a href="#" style="width:91px">About</a>
    <a href="#" class="active" style="width:91px">Bookings</a>
    <a href="#" style="width:90px">Free Trial</a>
    <a href="#" style="width:137px">Documentation</a>
    <a href="#" style="width:94px">Purchase</a>
    <a href="#" style="width:93px">Compare</a>
  </nav>

  <div class="steps">
    <div class="step"><span class="label">1. Details</span>
      <svg class="chevron" viewBox="0 0 22 45" aria-hidden="true"><polyline points="0,0 22,22.5 0,45" fill="var(--step-bg)" stroke="var(--step-line)" stroke-width="1"/></svg></div>
    <div class="step"><span class="label">2. Date &amp; Time</span>
      <svg class="chevron" viewBox="0 0 22 45" aria-hidden="true"><polyline points="0,0 22,22.5 0,45" fill="var(--step-bg)" stroke="var(--step-line)" stroke-width="1"/></svg></div>
    <div class="step current"><span class="label">3. Schedule</span>
      <svg class="chevron" viewBox="0 0 22 45" aria-hidden="true"><polyline points="0,0 22,22.5 0,45" fill="var(--step-bg)" stroke="var(--step-line)" stroke-width="1"/></svg></div>
    <div class="step"><span class="label">4. Confirm</span></div>
  </div>

  <section class="calendar">
    <div class="cal-title"><span class="arrow">◄</span><span>Friday &nbsp;-&nbsp; 4 November 2011</span><span class="arrow">►</span></div>
    <div class="cal-columns">
      <span>Time</span><span>Room 1</span><span>Room 2</span><span>Room 3</span><span>Room 4</span><span>Room 5</span>
    </div>
    <div class="cal-body">
      <div class="col-line" style="grid-column:2"></div>
      <div class="col-line" style="grid-column:3"></div>
      <div class="col-line" style="grid-column:4"></div>
      <div class="col-line" style="grid-column:5"></div>
      <div class="col-line" style="grid-column:6"></div>

      <div class="time" style="grid-row:1">9:00 am</div>
      <div class="time" style="grid-row:2">9:30 am</div>
      <div class="time" style="grid-row:3">10:00 am</div>
      <div class="time" style="grid-row:4">10:30 am</div>
      <div class="time" style="grid-row:5">11:00 am</div>
      <div class="time" style="grid-row:6">11:30 am</div>
      <div class="time" style="grid-row:7">12:00 pm</div>
      <div class="time" style="grid-row:8">12:30 pm</div>
      <div class="time" style="grid-row:9">1:00 pm</div>
      <div class="time" style="grid-row:10">1:30 pm</div>
      <div class="time" style="grid-row:11">2:00 pm</div>
      <div class="time" style="grid-row:12">2:30 pm</div>
      <div class="time" style="grid-row:13">3:00 pm</div>
      <div class="time" style="grid-row:14">3:30 pm</div>
      <div class="time" style="grid-row:15">4:00 pm</div>
      <div class="time" style="grid-row:16">4:30 pm</div>
      <div class="time" style="grid-row:17">5:00 pm</div>

      <article class="booking single" style="grid-column:2; grid-row:3 / 6">
        <h3>Bethany</h3>
        <ul><li>Manicure</li><li>Pedicure</li></ul>
      </article>
      <article class="booking group" style="grid-column:2; grid-row:7 / 10">
        <h3>Group - 2 People</h3>
        <ul><li>Head Massage</li><li>Scrub</li></ul>
      </article>
      <article class="booking group" style="grid-column:4; grid-row:2 / 6">
        <h3>Group - 4 People</h3>
        <ul><li>Indian Head Massage</li><li>Foot Rub</li><li>Scrub</li></ul>
      </article>
      <article class="booking single" style="grid-column:5; grid-row:4 / 7">
        <h3>Kevin</h3>
        <ul><li>Hot Stones</li><li>Massage</li></ul>
      </article>
      <article class="booking single" style="grid-column:3; grid-row:11 / 16">
        <h3>Angie</h3>
        <ul><li>Manicure</li><li>Full Body Scrub</li><li>Hot Stones</li></ul>
      </article>
    </div>
    <div class="cal-foot"></div>
  </section>

  <footer class="site-footer">
    <nav class="footer-nav">
      <a href="#">About</a><a href="#">Events</a><a href="#">Press</a><a href="#">Jobs</a>
      <a href="#">Staff</a><a href="#">Resources</a><a href="#">Privacy</a><a href="#">T&amp;Cs</a>
      <a href="#">Feedback</a><a href="#">Customer Service</a><a href="#">Contact</a>
    </nav>
    <span class="copyright">© 2011 Taro Reserve</span>
  </footer>

</body>
</html>
```